Top Pour Web site design

The aim of Top Pour is to provide an online service which allows customers to pre-order drinks and gain incentives such as fast entry, special offers (drinks, entry fees), as well as allowing customers to compare drinking establishments based upon costs and ratings.

what is required is the design of the pages stated below completed to the specifications.

Target Market(s)

The target market of Top Pour is men and women between the ages of 18 to 26 mainly. Within the age range of 18 to 26 the more specific target groups

Industry/Entity Type

Online

Requirements
Must have
• What is required to be designed

Website to be viewable on different systems e.g desktop, laptop and for mobile devices a mobile friendly page

Home page

Logo
Company name
Log in
Sign up
Help
Social media links, Follow us link

Bar, pub, club search function
Search by postcode, establishment type, distance

Pictorial instructions of how to use the site like ( quick dine). The stages are 1) select location 2) build order and pay 3) pick up from bar

Pre load results of establishments

Drinking establishment sign up

Map showing search results

List of results

My basket window which shows your order

Pop out box for customer sign up

Buttons for FAQ, general information, company information, Privacy policy ect at bottom of page

The home page is required to be Clear, simple, easy to use and stylish but not over the top with to much information which will confuse the customers. The preloaded results need to be obvious and where can be seen. The pictorial instructions should go below the preloaded results. Once the search criteria has been filled in and has been submitted the preloaded results and pictorial instructions will be removed and be replaced by the map and search results.

Drinking establishment personal page requires

Details of drinking establishment (name, address, contact, map)
list of drinks avliable
My basket
Special Offers
Gallery
Calendar
Reviews section at the bottom

When a person clicks on a drinking establishment page what that person should see when they open the page is company name logo
with a list of the drinks they offer and special offers. Tabs or buttons for gallery, establishment details, calender and special offers should be located along top or down the left. when they are clicked on they will replace the menu.

The colour scheme is based around the logo which is attached. We do not want any pink or overly bright colours which would not go with the logo.

A site which we like is this one
http://www.quick-dine.example.co.uk/
this site is perfect simple, clear but also good looking. If you need inspiration you should use this site as a starting point.
Should not have
• what should be avoided is a site which like this one http://platepoint.example.co.uk/~beta/?gclid=XQMWpLaRtnfGDsHYbTqeKZPLv

it is to complicated with bad font and colours. The site just feels cheesy and not classy. we like very little about this site

```html
<!DOCTYPE html>
<html lang="en">
<head>
<meta charset="utf-8">
<title>Top Pour – Order your round online</title>
<link href="https://fonts.googleapis.com/css2?family=Open+Sans:wght@400;600;700&family=Cabin+Sketch:wght@400;700&family=Gochi+Hand&family=Schoolbell&display=swap" rel="stylesheet">
<style>
:root{
  --brand:#2e3192;
  --brand-dark:#1c1f78;
  --ink:#333333;
  --muted:#777777;
  --gold:#c8960c;
  --card-line:#dddddd;
  --paper:#ffffff;
  --bg-fade:#e2e2e2;
  --icon-grey:#9a9a9a;
  --off:#c4c4c4;
}
*{box-sizing:border-box;margin:0;padding:0}
html,body{width:1200px;height:1125px;overflow:hidden;background:#fff}
body{font-family:"Open Sans",Arial,sans-serif;color:var(--ink)}
.page{position:relative;width:1200px;height:1125px;overflow:hidden;
  background:linear-gradient(#fff 0,#fff 650px,var(--bg-fade) 1010px)}
.top-edge{position:absolute;left:0;top:0;width:1200px;height:6px;background:#c9c9c9}

/* header */
.brand{position:absolute;left:188px;top:48px;display:flex;align-items:center;gap:10px}
.brand-mark{width:62px;height:62px;border-radius:50%;background:#a8a8a8}
.brand-name{font-size:32px;font-weight:600;color:var(--brand)}
.social{position:absolute;display:flex;gap:5px}
.social span{display:block;border-radius:50%}
.social.head{left:702px;top:59px}
.social.head span{width:22px;height:22px;background:var(--icon-grey)}
.account{position:absolute;left:825px;top:60px;font-size:15px;font-weight:600;color:#444}
.help{position:absolute;left:937px;top:59px;width:82px;height:25px;border:1px solid #cfcfcf;border-radius:4px;
  font-size:12px;color:var(--brand);text-align:center;line-height:23px;background:#fff;box-shadow:0 1px 2px rgba(0,0,0,.15)}

/* search */
.search{position:absolute;left:184px;top:124px;width:636px;height:137px}
.search svg{position:absolute;inset:0}
.search h1{position:absolute;left:27px;top:14px;font-family:"Schoolbell",cursive;font-size:40px;color:#fff;font-weight:400;letter-spacing:.5px}
.field{position:absolute;top:72px;height:32px;background:#fff;border:1px solid #bbb;font-size:14px;color:#666;padding:5px 9px}
.field.select::after{content:"";position:absolute;right:8px;top:13px;border:4px solid transparent;border-top:6px solid #333}
.search-btn{position:absolute;left:445px;top:72px;width:157px;height:32px;border-radius:3px;
  background:linear-gradient(#4d52c9,#3236a8);border:1px solid #7b80e6;color:#fff;font-weight:700;font-size:16px;
  display:flex;align-items:center;justify-content:center;gap:8px;letter-spacing:.3px}

/* basket */
.basket{position:absolute;left:830px;top:122px;width:178px;height:142px;background:#fbfbfb;transform:rotate(-1deg);
  box-shadow:2px 4px 6px rgba(0,0,0,.25)}
.basket .pin{position:absolute;left:82px;top:3px;width:10px;height:18px;border-radius:5px;background:var(--brand-dark)}
.basket h2{position:absolute;left:25px;top:29px;font-family:"Gochi Hand",cursive;font-weight:400;font-size:20px;color:var(--brand)}
.basket dl{position:absolute;left:27px;top:58px;font-size:12px;color:#666;display:grid;grid-template-columns:62px auto;row-gap:6px}
.basket dd{color:#2b4fd6;font-weight:600}
.checkout{position:absolute;left:27px;top:104px;width:73px;height:24px;border:1px solid #bbb;background:linear-gradient(#f2f2f2,#dcdcdc);
  font-size:12px;color:#555;text-align:center;line-height:22px}

/* establishments */
.section-title{position:absolute;font-family:"Cabin Sketch",cursive;font-weight:700;font-size:40px;color:#4a4a4a}
.listing-title{left:184px;top:283px}
.venue{position:absolute;width:262px;height:129px;border:1px solid var(--card-line);background:#fff}
.venue .photo{position:absolute;left:10px;top:13px;width:58px;height:58px;box-shadow:1px 2px 3px rgba(0,0,0,.3)}
.venue h3{position:absolute;left:76px;top:8px;font-size:17px;font-weight:700;color:var(--brand-dark);white-space:nowrap}
.venue dl{position:absolute;left:76px;top:34px;display:grid;grid-template-columns:92px auto;row-gap:2px;font-size:12.5px;line-height:18.5px}
.venue dt{font-weight:700;color:#444}
.venue dd::before{content:": "}
.cost{color:var(--gold);font-weight:700}
.rating{display:inline-flex;gap:3px;vertical-align:-1px}
.rating i{display:block;width:10px;height:9px;border-radius:1px 1px 3px 3px;background:#4b53d6}
.rating i.off{background:var(--off)}

/* how it works */
.how-title{left:0;width:1200px;text-align:center;top:665px;color:var(--brand);font-size:42px}
.step{position:absolute;top:745px;width:264px;height:200px}
.step svg.sheet{position:absolute;inset:0}
.step .num{position:absolute;left:31px;top:20px;width:28px;height:32px;border-radius:50%;background:var(--brand);color:#fff;
  font-family:"Gochi Hand",cursive;font-size:22px;text-align:center;line-height:32px}
.step .art{position:absolute;left:70px;top:30px;width:130px;height:100px;border-radius:8px}
.step p{position:absolute;left:0;right:0;top:140px;text-align:center;font-family:"Gochi Hand",cursive;font-size:22px;color:#555}
.chevron{position:absolute;top:826px}

/* footer */
.footer{position:absolute;left:0;top:1008px;width:1200px;height:117px}
.footer svg{position:absolute;inset:0}
.footer nav{position:absolute;left:181px;top:49px;font-size:13px;color:#fff}
.footer nav a{color:#fff;text-decoration:none}
.footer small{position:absolute;left:181px;top:70px;font-size:13px;color:#a9acd9}
.social.foot{left:905px;top:54px}
.social.foot span{width:23px;height:23px;background:#fff}
</style>
</head>
<body>
<div class="page">
  <div class="top-edge"></div>

  <header>
    <div class="brand"><span class="brand-mark"></span><span class="brand-name">Top Pour</span></div>
    <div class="social head" aria-label="Follow us"><span></span><span></span><span></span><span></span></div>
    <div class="account">Log in . Sign up</div>
    <div class="help">NEED HELP</div>
  </header>

  <section class="search">
    <svg width="636" height="137" viewBox="0 0 636 137" aria-hidden="true">
      <path fill="var(--brand)" d="M4 6 L60 3 L120 7 L190 2 L260 6 L330 3 L400 7 L470 2 L540 6 L600 3 L633 7 L629 40 L634 80 L630 110 L634 131 L560 134 L480 129 L400 135 L320 130 L240 135 L160 129 L80 134 L2 130 L6 95 L2 60 L5 30 Z"/>
    </svg>
    <h1>Order your round online</h1>
    <div class="field" style="left:29px;width:122px">Your Postcode</div>
    <div class="field select" style="left:156px;width:156px">Establishment Type</div>
    <div class="field select" style="left:316px;width:120px">Distance</div>
    <div class="search-btn">SEARCH NOW
      <svg width="16" height="16" viewBox="0 0 16 16" aria-hidden="true"><circle cx="6.5" cy="6.5" r="4.8" fill="none" stroke="#fff" stroke-width="2"/><path d="M10 10 L14.5 14.5" stroke="#fff" stroke-width="2.5" stroke-linecap="round"/></svg>
    </div>
  </section>

  <aside class="basket">
    <span class="pin"></span>
    <h2>Your Basket</h2>
    <dl><dt>items</dt><dd>: 0</dd><dt>Subtotal</dt><dd>: £0.0</dd></dl>
    <div class="checkout">Checkout</div>
  </aside>

  <h2 class="section-title listing-title">Drinking establishment</h2>

  <article class="venue" style="left:185px;top:351px">
    <div class="photo" role="img" aria-label="Photo of the pub frontage" style="background:linear-gradient(#6d6a66,#2d2b2a)"></div>
    <h3>The LANTERN</h3>
    <dl><dt>Provides</dt><dd>Food &amp; Drink</dd><dt>Special offers</dt><dd>15% Off</dd>
      <dt>Cost</dt><dd class="cost">£ £ £</dd>
      <dt>Rating</dt><dd><span class="rating"><i></i><i></i><i></i><i></i><i class="off"></i></span></dd></dl>
  </article>
  <article class="venue" style="left:468px;top:351px">
    <div class="photo" role="img" aria-label="Photo of the pub building" style="background:linear-gradient(#c9c7bf,#8b8372 70%,#5a3a30)"></div>
    <h3>HARTWELL ARMS</h3>
    <dl><dt>Provides</dt><dd>Food &amp; Drink</dd><dt>Special offers</dt><dd>20% Off</dd>
      <dt>Cost</dt><dd class="cost">£ £ £ £</dd>
      <dt>Rating</dt><dd><span class="rating"><i></i><i></i><i></i><i></i><i></i></span></dd></dl>
  </article>
  <article class="venue" style="left:751px;top:351px">
    <div class="photo" role="img" aria-label="Photo of the pub shopfront" style="background:linear-gradient(#4a4643,#d8d2c6 55%,#2f2b28)"></div>
    <h3>The LANTERN</h3>
    <dl><dt>Provides</dt><dd>Food &amp; Drink</dd><dt>Special offers</dt><dd>8% Off</dd>
      <dt>Cost</dt><dd class="cost">£</dd>
      <dt>Rating</dt><dd><span class="rating"><i></i><i></i><i></i><i class="off"></i><i class="off"></i></span></dd></dl>
  </article>

  <article class="venue" style="left:185px;top:501px">
    <div class="photo" role="img" aria-label="Photo of the bar interior at night" style="background:linear-gradient(135deg,#7a3a44,#2a1a1c)"></div>
    <h3>ROSE &amp; THISTLE</h3>
    <dl><dt>Provides</dt><dd>Food &amp; Drink</dd><dt>Special offers</dt><dd>10% Off</dd>
      <dt>Cost</dt><dd class="cost">£ £ £ £ £</dd>
      <dt>Rating</dt><dd><span class="rating"><i></i><i></i><i></i><i></i><i></i></span></dd></dl>
  </article>
  <article class="venue" style="left:468px;top:501px">
    <div class="photo" role="img" aria-label="Photo of live music in the club" style="background:radial-gradient(circle at 50% 30%,#e07aa0,#5a2040 60%,#1e0f1a)"></div>
    <h3 style="top:6px">FIDDLEHOUSE</h3>
    <dl style="top:32px"><dt>Provides</dt><dd>Food &amp; Drink</dd><dt>Special offers</dt><dd>12% Off</dd>
      <dt>Cost</dt><dd class="cost">£ £ £</dd>
      <dt>Rating</dt><dd><span class="rating"><i></i><i></i><i></i><i class="off"></i><i class="off"></i></span></dd></dl>
  </article>
  <article class="venue" style="left:751px;top:501px">
    <div class="photo" role="img" aria-label="Photo of the pub on a street corner" style="background:linear-gradient(#5a6068,#2e3338)"></div>
    <h3 style="top:6px">EARL OF DARROW</h3>
    <dl style="top:32px"><dt>Provides</dt><dd>Food &amp; Drink</dd><dt>Special offers</dt><dd>18% Off</dd>
      <dt>Cost</dt><dd class="cost">£ £ £ £ £</dd>
      <dt>Rating</dt><dd><span class="rating"><i></i><i></i><i></i><i></i><i class="off"></i></span></dd></dl>
  </article>

  <h2 class="section-title how-title">How it Works</h2>

  <div class="step" style="left:176px">
    <svg class="sheet" width="264" height="200" viewBox="0 0 264 200" aria-hidden="true">
      <path d="M12 195 L266 200 L266 203 L12 200 Z" fill="#999" opacity=".5"/>
    <path d="M22 10 L254 7 L262 195 L0 182 Z" fill="#fff"/>
      <rect x="90" y="-8" width="98" height="22" fill="#d0d0d0" opacity=".8"/>
    </svg>
    <span class="num">1</span>
    <div class="art" role="img" aria-label="Illustration of a map with a magnifying glass" style="background:linear-gradient(135deg,#8cc05a,#4f8f3a 60%,#6fb0d8)"></div>
    <p>Select Location</p>
  </div>
  <svg class="chevron" style="left:418px" width="30" height="40" viewBox="0 0 30 40" aria-hidden="true"><path d="M4 2 L26 20 L4 38 L4 28 L14 20 L4 12 Z" fill="#b8b0b0"/></svg>

  <div class="step" style="left:464px">
    <svg class="sheet" width="264" height="200" viewBox="0 0 264 200" aria-hidden="true">
      <path d="M22 10 L254 7 L262 195 L0 182 Z" fill="#fff"/>
      <rect x="90" y="-8" width="98" height="22" fill="#d0d0d0" opacity=".8"/>
    </svg>
    <span class="num">2</span>
    <div class="art" role="img" aria-label="Illustration of a cash register" style="background:linear-gradient(#f2e38c,#c9d3df 45%,#8ea2bd)"></div>
    <p>build order and pay</p>
  </div>
  <svg class="chevron" style="left:703px" width="30" height="40" viewBox="0 0 30 40" aria-hidden="true"><path d="M4 2 L26 20 L4 38 L4 28 L14 20 L4 12 Z" fill="#b8b0b0"/></svg>

  <div class="step" style="left:752px">
    <svg class="sheet" width="264" height="200" viewBox="0 0 264 200" aria-hidden="true">
      <path d="M22 10 L254 7 L262 195 L0 182 Z" fill="#fff"/>
      <rect x="90" y="-8" width="98" height="22" fill="#d0d0d0" opacity=".8"/>
    </svg>
    <span class="num">3</span>
    <div class="art" role="img" aria-label="Illustration of two glasses of red wine" style="background:linear-gradient(#f4f4f4,#b0304a 45%,#f0e6a0)"></div>
    <p>pick up from bar</p>
  </div>

  <footer class="footer">
    <svg width="1200" height="117" viewBox="0 0 1200 117" aria-hidden="true">
      <path fill="var(--brand)" d="M0 6 L40 3 L90 7 L150 2 L210 6 L280 3 L350 7 L420 2 L490 6 L560 3 L630 7 L700 2 L770 6 L840 3 L910 7 L980 2 L1050 6 L1120 3 L1200 6 L1200 117 L0 117 Z"/>
    </svg>
    <nav><a href="#">FAQ</a> | <a href="#">general information</a> | <a href="#">company information</a> | <a href="#">Privacy policy</a></nav>
    <small>Copyright © 2013 Top Pour. All rights reserved</small>
    <div class="social foot" aria-label="Follow us"><span></span><span></span><span></span><span></span></div>
  </footer>
</div>
</body>
</html>
```